Core Value Graphic for a Service Disabled and Minority Certified contractor

My company, Keystone Aid Partners, is a US Federal Contractor that hires veterans and service disabled veterans. Our website is www.keystoneaid7.example. We work hard to maintain a 50:50 split between veterans and non-veterans on our team. Our tagline is "To Find a Better Way." We are continually looking to integrate technology and efficiency into all that we do.

I want a way to express our company core values visually so that our employees and customers alike can read them and get a sense of who we are, what drives us to succeed, and what makes up our team DNA.

I need an artist like you to help me represent our core values visually. In a manner that I can print it out on an 8"X11" sheet of paper or a large 48" X 48" poster, without losing the visual clarity or that it pixelates out of focus. I am looking for a color scheme that is patriotic with Red, White, and Blues and similar hues. I would also like to incorporate my logo and tagline into the design in some manner.

I have attached several examples of a Core Value Grids from other companies. I am hopeful it will inspire you, and a get your brain juices flowing to provide me with a knockout Core Value Grid that will rock only you can provide! I also include a copy of my company Core Values and a copy of our Logo.

Looking forward to seeing your creations. Thanks.

Target Market(s)

Employees, any potential strategic alliance partners, and customers.

Industry/Entity Type

Contractor

Requirements
Must have
• Patriotic feel and have my logo someplace on the document.

```html
<!DOCTYPE html>
<html lang="en">
<head>
<meta charset="utf-8">
<title>Keystone Aid Partners – Our Core Values</title>
<link href="https://fonts.googleapis.com/css2?family=Arimo:wght@700&family=Open+Sans:wght@700;800&display=swap" rel="stylesheet">
<style>
  :root{
    --page:#efefef;
    --navy:#1b2a55;
    --navy-deep:#141b3c;
    --red:#b01c22;
    --red-dark:#7a1014;
    --white:#ffffff;
    --ink:#1a1a1a;
    --head-red:#b3161c;
    --ghost:rgba(255,255,255,.26);
  }
  html,body{margin:0;padding:0;width:1200px;height:1000px;overflow:hidden;background:var(--page);}
  .poster{position:absolute;left:205px;top:100px;width:788px;height:790px;background:var(--navy-deep);overflow:hidden;}
  .poster__header{position:absolute;left:0;top:0;width:100%;height:100px;
    background:linear-gradient(90deg,#fff 0%,#e8e8f0 25%,#8a8fb5 50%,#3a3d5c 72%,#111 100%);}
  .brand{position:absolute;left:28px;top:28px;display:flex;align-items:center;gap:10px;}
  .brand__mark{width:24px;height:24px;background:var(--red);flex:none;}
  .brand__name{font-family:"Open Sans",sans-serif;font-weight:800;font-size:19px;color:var(--navy);
    letter-spacing:.3px;line-height:1.1;}
  .poster__title{position:absolute;right:18px;top:24px;margin:0;font-family:"Arimo",sans-serif;font-weight:700;
    font-size:50px;color:var(--white);line-height:1;white-space:nowrap;text-shadow:0 0 2px rgba(0,0,0,.45);}
  .poster__field{position:absolute;left:0;top:100px;width:100%;height:690px;
    background:radial-gradient(ellipse at 85% 30%,rgba(176,28,34,.75),transparent 45%),
               radial-gradient(ellipse at 10% 95%,rgba(176,28,34,.7),transparent 40%),
               radial-gradient(ellipse at 20% 25%,rgba(60,80,150,.45),transparent 45%),
               linear-gradient(135deg,#1d2550 0%,#151b3c 55%,#3a1426 100%);}
  .rule{position:absolute;left:0;width:100%;height:2px;background:#d9d9e3;}
  .rule--top{top:110px;} .rule--bottom{top:778px;}
  .ghost-title{position:absolute;left:30px;top:696px;margin:0;font-family:"Arimo",sans-serif;font-weight:700;
    font-size:68px;color:var(--ghost);line-height:1;white-space:nowrap;}
  .links{position:absolute;left:0;top:0;width:788px;height:790px;}
  .value{position:absolute;}
  .value__tag{position:absolute;top:0;left:5px;z-index:2;background:linear-gradient(90deg,var(--red),var(--red-dark));
    color:var(--white);font-family:"Arimo",sans-serif;font-weight:700;font-size:11px;line-height:1.15;
    text-align:center;padding:3px 10px;white-space:nowrap;}
  .value__card{position:absolute;left:0;top:27px;background:var(--white);box-sizing:border-box;padding:6px 9px 8px;
    text-align:center;font-family:"Open Sans",sans-serif;font-weight:700;font-size:7.6px;line-height:1.42;
    color:var(--ink);text-transform:uppercase;}
  .value__card h3{margin:0 0 3px;font-family:"Open Sans",sans-serif;font-weight:800;font-size:10.5px;
    color:var(--head-red);line-height:1.1;}
  .value__card p{margin:0 0 4px;}
  .value__card p:last-child{margin-bottom:0;}
  .tagline{position:absolute;left:325px;top:386px;width:140px;text-align:center;font-family:"Arimo",sans-serif;
    font-weight:700;font-size:20px;line-height:1.2;color:var(--white);}
</style>
</head>
<body>
<main class="poster">
  <header class="poster__header">
    <div class="brand"><span class="brand__mark"></span><span class="brand__name">KEYSTONE AID<br>PARTNERS</span></div>
    <h1 class="poster__title">OURS CORE VALUES</h1>
  </header>
  <div class="poster__field" role="img" aria-label="Dark navy field with soft red and blue sweeping bands"></div>
  <div class="rule rule--top"></div>
  <div class="rule rule--bottom"></div>
  <p class="ghost-title" aria-hidden="true">OURS CORE VALUES</p>

  <svg class="links" viewBox="0 0 788 790" aria-hidden="true">
    <defs>
      <symbol id="star" viewBox="-20 -20 40 40">
        <polygon points="0,-19 4.5,-6 18,-6 7,2.5 11,16 0,8 -11,16 -7,2.5 -18,-6 -4.5,-6" fill="#fff"/>
        <polygon points="0,-12 2.8,-3.8 11.4,-3.8 4.4,1.6 7,10 0,5 -7,10 -4.4,1.6 -11.4,-3.8 -2.8,-3.8" fill="#1b2a55"/>
      </symbol>
    </defs>
    <g stroke="#fff" stroke-width="1.5" fill="none">
      <polyline points="345,245 370,245 370,317 390,330"/>
      <polyline points="470,395 515,395 515,362"/>
      <polyline points="268,467 310,467 310,430"/>
      <polyline points="373,508 373,494"/>
      <polyline points="420,490 470,490 526,490"/>
    </g>
    <g fill="#fff">
      <circle cx="345" cy="245" r="4"/>
      <circle cx="268" cy="467" r="4"/>
      <circle cx="373" cy="512" r="4"/>
      <circle cx="522" cy="490" r="4"/>
      <circle cx="515" cy="362" r="4"/>
    </g>
    <polygon points="390,355 455,402 430,480 350,480 325,402" fill="#1e3a78" stroke="#fff" stroke-width="1"/>
    <use href="#star" x="368" y="315" width="44" height="44"/>
    <use href="#star" x="290" y="375" width="44" height="44"/>
    <use href="#star" x="446" y="375" width="44" height="44"/>
    <use href="#star" x="318" y="465" width="44" height="44"/>
    <use href="#star" x="416" y="465" width="44" height="44"/>
  </svg>

  <div class="tagline">TO FIND<br>A BETTER<br>WAY</div>

  <section class="value" style="left:90px;top:122px;">
    <div class="value__tag">Everyone comes back<br>to the Green Zone.</div>
    <div class="value__card" style="width:248px;">
      <h3>WHAT IT MEANS</h3>
      <p>Safety takes precedence over every phase of the day's operation.</p>
      <h3>HOW TO EXPRESS IT</h3>
      <p>Anyone can call a stop to the work in progress if an unsafe act is occurring. In fact, it is each team member's duty to do so, rectify the unsafe issue, then proceed. Never hesitate; everyone comes back. Finally, each after action review begins with discussing safety issues. We always let everyone on the team know of an unsafe situation, so it can be avoided in the future.</p>
      <h3>RESULT</h3>
      <p>All team members go home to their loved ones each day to pursue their individual happiness</p>
    </div>
  </section>

  <section class="value" style="left:449px;top:122px;">
    <div class="value__tag" style="padding:3px 30px;">Boldly go.<br>Seek. Find.</div>
    <div class="value__card" style="width:247px;">
      <h3>WHAT IT MEANS</h3>
      <p>We weave innovation into the fabric that makes up our company.</p>
      <h3>HOW TO EXPRESS IT</h3>
      <p>We're early adopters of technology. We quickly evaluate new technologies or processes that could separate us from our competition. Then we implement and evaluate these new technologies. We dump it quickly if we see it is nothelping us achieve "Commander's Intent." We have the guts to be first. We iterate continuously and attack, attack, attack.</p>
      <h3>RESULT</h3>
      <p>We will be ahead of our competition. It' one mechanism that helps us scale. Prosperity favors the bold!</p>
    </div>
  </section>

  <section class="value" style="left:20px;top:374px;">
    <div class="value__tag" style="left:10px;padding:3px 16px;">Never leave your<br>wingman.</div>
    <div class="value__card" style="width:236px;">
      <h3>WHAT IT MEANS</h3>
      <p>We always help your team members be successful. Commitment to each other and to our own personal integrity is the fuel that empowers us.</p>
      <h3>HOW TO EXPRESS IT</h3>
      <p>If a wingman is having challenges accomplishing their individual priorities or completing their assigned mission, volunteer to helpthem to do so. This goes for subs/suppliers as well. We help those who help us succeed! Always look to establish the best win-win relationship possible, and do what you can to support them if they get into a bind.</p>
      <h3>RESULT</h3>
      <p>Be there for them and they will be there for us.</p>
    </div>
  </section>

  <section class="value" style="left:526px;top:390px;">
    <div class="value__tag">Troops (Team Members)<br>eat first.</div>
    <div class="value__card" style="width:238px;">
      <h3>WHAT IT MEANS</h3>
      <p>No leader will put themselves ahead of their subordinates.</p>
      <h3>HOW TO EXPRESS IT</h3>
      <p>We lead by example. Demonstrate the moral courage and discipline to do the right thing at the highest level of quality.</p>
      <h3>RESULT</h3>
      <p>Every new team member's will quickly realize their leaders genuinely care for their welfare and success. This is the best way to drive esprit de corps and achieve excellence.</p>
    </div>
  </section>

  <section class="value" style="left:270px;top:520px;">
    <div class="value__tag" style="left:10px;padding:3px 30px;">Fail quickly<br>and learn</div>
    <div class="value__card" style="width:242px;">
      <h3>WHAT IT MEANS</h3>
      <p>If you're not making mistakes, you're not taking enough chances or getting out of your comfort zone.</p>
      <h3>HOW TO EXPRESS IT</h3>
      <p>Use your best judgment when trying something new. But, don't let your pride keep you from saying, "I was wrong" when your idea doesn't work. We trust you will know when it's time to dump the idea, or stop doing something that doesn't work.</p>
      <h3>RESULT</h3>
      <p>No one will ever be penalized for making a mistake. Don't be afraid to try something you believe will work. That's how we grow ourselves and our team members.</p>
    </div>
  </section>
</main>
</body>
</html>
```